Direct Mail Condition Reporting Flyer

This is a quality control service that is designed to
detect direct mail such as letters, magazines and catalogs that are delivered by the Vellmark Courier Bureau in poor condition. Attached are actual samples of mail delivered in poor condition and our company logo. We generally use the Red and Blue colors of the Vellmark Courier Bureau.

Target Market(s)

Direct mailers from every Industry

Industry/Entity Type

It Service

Font styles to use
Sans Serif

Colors
ec1f27
0555a3

Requirements
Must have
• It needs to look professional. It will be placed on a table at a trade conference and inserted into a folder with other material.

```html
<!DOCTYPE html>
<html lang="en">
<head>
<meta charset="utf-8">
<title>Vantage Mailwatch – Direct Mail Condition Reporting</title>
<link href="https://fonts.googleapis.com/css2?family=Inter:wght@400;600;700;800&display=swap" rel="stylesheet">
<style>
  :root {
    --brand-red: #c1183a;
    --brand-blue: #1a3f8a;
    --ink-grey: #7b7c80;
    --ink-dark: #3a3a3c;
    --paper: #ffffff;
  }
  * { margin: 0; padding: 0; box-sizing: border-box; }
  html, body {
    width: 792px;
    height: 1200px;
    overflow: hidden;
    background: var(--paper);
  }
  .flyer {
    position: relative;
    width: 792px;
    height: 1200px;
    background: var(--paper);
    font-family: "Inter", Arial, sans-serif;
  }
  .check-graphic {
    position: absolute;
    inset: 0;
    width: 792px;
    height: 1200px;
  }
  .check-graphic .field { fill: var(--brand-blue); }
  .check-graphic .tick { fill: var(--brand-red); }
  .brand {
    position: absolute;
    left: 45px;
    top: 134px;
  }
  .brand-name {
    display: flex;
    align-items: center;
    gap: 10px;
    color: var(--brand-blue);
    font-weight: 800;
    font-size: 24px;
    line-height: 28px;
    letter-spacing: 1.5px;
    text-transform: uppercase;
  }
  .brand-mark {
    width: 13px;
    height: 13px;
    background: var(--brand-red);
  }
  .brand-tagline {
    margin: 8px 0 0 165px;
    font-size: 10.5px;
    font-weight: 600;
    color: var(--ink-dark);
    letter-spacing: 0.1px;
  }
  .headline {
    position: absolute;
    left: 57px;
    top: 256px;
    font-size: 48px;
    line-height: 45px;
    font-weight: 800;
    letter-spacing: -0.5px;
    color: var(--ink-grey);
  }
</style>
</head>
<body>
  <main class="flyer">
    <svg class="check-graphic" viewBox="0 0 792 1200" aria-hidden="true">
      <polygon class="field" points="0,581 135,581 201,679 693,0 792,0 792,1139 0,1139"/>
      <polygon class="tick" points="0,581 135,581 201,679 693,0 792,0 233,817 171,817"/>
    </svg>

    <header class="brand">
      <div class="brand-name"><span class="brand-mark"></span>Vantage Mailwatch</div>
      <p class="brand-tagline">Insight that Keeps Your Mail Moving.</p>
    </header>

    <h1 class="headline">How much<br>of your mail<br>is being<br>delivered<br>like this?</h1>
  </main>
</body>
</html>
```